"Copper Lantern" Play - Poster Design for Theatre Group

We are an amateur theatre group based in Geneva, Switzerland. We take pride in eye-catching posters for our shows, which are printed in various sizes.
This design will be for a play in March 2016. The play is called "Copper Lantern", and it's a Marwick Medal winner from Martin Crowe-Fenwick. The play is about a couple who have everything a family could want, until they lose a child in a life-shattering accident that turns their world upside down. The play charts the couple's bittersweet search to find each other and to find comfort.
Most importantly, we want a design that will make people want to see the show. We don't want to give away the plot or be too heavy-handed about death, but we want it to be clear that it's not a comedy (although there are some lighter moments!).
Attached you will find a template for the poster. This simply has our group name and logo in the top right corner: (Lakeside Stage Players Guild presents).
You may change the color of both the text and the logo, but please do not change the font, size, or location.
Here is the information that needs to be on the poster, wherever you see fit:
play title: Copper Lantern
author byline: by Martin Crowe-Fenwick
director line: directed by Ned Pilbury
tagline: How do you keep it together when your whole world's fallen apart?
dates and times:
1-5 March 2016
(Tue-Fri 20:00, Sat 19:00)
location:
Théâtre du Colibri
Eaux-Vives, Geneva
websites:
www.lspg.ch
www.scenesansfrontiere.ch
Technical Details:
Any font or combination of fonts is acceptable. The largest text should be the play title. The author's name must be at least 50% of the title font size.
For this competition, we would like the version with A3 proportions, which will also be used at F4 (89.5 x 128 cm) and A5 sizes (14.8 x 21 cm). Therefore no text should be below 9pt at A5.
However, from the winning designer we will also need repurposed sizes of the same design. Here is a comprehensive list of the sizes we will need.
1) A3 print poster. Artwork should be 300dpi, CMYK, sent with a 1mm bleed all round, to specification PDF/X-1A:2001. We will need this image in PDF format in addition to the default Artmarketo formats.
2) Chatterbook advert picture. 1200px by 628px, RGB jpeg. This must comply with Chatterbook’s restrictions on amount of text, which is no more than 20% of area taken up by text.(https://www.chatterbook-example.com/ads/tools/text_overlay).
Because of these restrictions it is sufficient to include just the title and the author's name in this version.
3) Chatterbook cover picture: 851px by 314px. RGB jpeg. It is sufficient to include just the title and the author's name in this version.
4) Web banner. 1000px by 300px. RGB jpeg. This version should include just the main image(s), no text.

```html
<!DOCTYPE html>
<html lang="en">
<head>
<meta charset="utf-8">
<title>Copper Lantern – Poster</title>
<link rel="stylesheet" href="https://fonts.googleapis.com/css2?family=Oswald:wght@400;500;700&family=Playfair+Display:ital,wght@1,400;1,700&display=swap">
<style>
  :root {
    --paper: #ddd3c2;
    --paper-edge: #b9ab94;
    --ink: #3a2f27;
    --ink-soft: #5a4c40;
    --accent: #ad2a1f;
    --light: #fff6e6;
    --tunnel-dark: #2a1f16;
    --tunnel-mid: #7a5f43;
    --tunnel-glow: #fdf4e2;
  }
  html, body {
    margin: 0;
    padding: 0;
    overflow: hidden;
  }
  body {
    width: 851px;
    height: 1200px;
    background: var(--paper);
  }
  .poster {
    position: relative;
    width: 851px;
    height: 1200px;
    overflow: hidden;
    background: radial-gradient(ellipse at 50% 45%, #e8dfcf 0%, var(--paper) 55%, var(--paper-edge) 100%);
    font-family: "Oswald", sans-serif;
    color: var(--ink);
  }

  /* Group mark */
  .presenter {
    position: absolute;
    top: 30px;
    right: 56px;
    display: flex;
    align-items: center;
    gap: 14px;
  }
  .presenter-name {
    text-align: right;
    font-family: "Oswald", sans-serif;
    font-weight: 500;
    font-size: 17px;
    line-height: 1.15;
    color: var(--ink);
  }
  .presenter-dot {
    width: 64px;
    height: 64px;
    border-radius: 50%;
    border: 4px solid var(--ink);
    box-sizing: border-box;
  }

  /* Title block */
  .title {
    position: absolute;
    top: 290px;
    left: 0;
    width: 100%;
    margin: 0;
    text-align: center;
    font-family: "Oswald", sans-serif;
    font-weight: 700;
    font-size: 84px;
    line-height: 1;
    letter-spacing: 1px;
    color: var(--ink);
    text-transform: uppercase;
  }
  .byline {
    position: absolute;
    top: 396px;
    left: 0;
    width: 100%;
    text-align: center;
    font-size: 30px;
    color: var(--ink);
  }
  .byline-by {
    font-family: "Playfair Display", serif;
    font-style: italic;
    font-size: 26px;
    margin-right: 6px;
  }
  .byline-name {
    font-family: "Oswald", sans-serif;
    font-weight: 700;
    text-transform: uppercase;
    letter-spacing: 1px;
  }

  /* Image band */
  .scene {
    position: absolute;
    top: 438px;
    left: 0;
    width: 851px;
    height: 432px;
  }
  .tagline {
    position: absolute;
    top: 490px;
    left: 205px;
    margin: 0;
    font-family: "Playfair Display", serif;
    font-style: italic;
    font-size: 22px;
    line-height: 42px;
    color: var(--light);
  }

  /* Credits */
  .director {
    position: absolute;
    top: 876px;
    left: 0;
    width: 100%;
    text-align: center;
  }
  .director-label {
    display: block;
    font-family: "Playfair Display", serif;
    font-style: italic;
    font-size: 17px;
    line-height: 1.1;
  }
  .director-name {
    display: block;
    font-weight: 700;
    font-size: 24px;
    letter-spacing: 1px;
    text-transform: uppercase;
  }
  .dates {
    position: absolute;
    top: 936px;
    left: 0;
    width: 100%;
    text-align: center;
    font-weight: 700;
    font-size: 46px;
    line-height: 1;
    color: var(--accent);
    letter-spacing: 1px;
  }
  .times {
    position: absolute;
    top: 988px;
    left: 0;
    width: 100%;
    text-align: center;
    font-weight: 500;
    font-size: 17px;
    letter-spacing: 1px;
    text-transform: uppercase;
  }
  .venue {
    position: absolute;
    top: 1012px;
    left: 0;
    width: 100%;
    text-align: center;
    font-family: "Playfair Display", serif;
    font-style: italic;
    font-weight: 700;
    font-size: 22px;
  }
  .links {
    position: absolute;
    top: 1074px;
    left: 0;
    width: 100%;
    text-align: center;
    font-size: 15px;
    line-height: 20px;
    color: var(--ink-soft);
  }
  .links b {
    font-weight: 700;
    color: var(--ink);
  }
</style>
</head>
<body>
<main class="poster">
  <div class="presenter">
    <div class="presenter-name">Lakeside Stage<br>Players Guild<br>presents</div>
    <div class="presenter-dot"></div>
  </div>

  <h1 class="title">Copper Lantern</h1>
  <div class="byline"><span class="byline-by">by</span><span class="byline-name">Martin Crowe-Fenwick</span></div>

  <svg class="scene" viewBox="0 0 851 432" role="img" aria-label="Photograph of two figures silhouetted walking into a glowing sepia tunnel, framed with torn paper edges">
    <defs>
      <radialGradient id="tunnel-light" cx="0.62" cy="0.5" r="0.7">
        <stop offset="0" stop-color="var(--tunnel-glow)"/>
        <stop offset="0.12" stop-color="#e6cfa8"/>
        <stop offset="0.4" stop-color="var(--tunnel-mid)"/>
        <stop offset="1" stop-color="var(--tunnel-dark)"/>
      </radialGradient>
    </defs>
    <polygon fill="url(#tunnel-light)" points="0,18 40,10 85,22 130,6 180,16 240,4 300,20 360,8 420,18 470,2 530,14 590,6 650,22 710,8 770,18 820,6 851,14 851,420 805,428 760,414 700,426 640,412 580,430 520,416 460,428 400,410 340,424 280,414 220,430 160,412 100,426 50,414 0,424"/>
  </svg>

  <p class="tagline">How do you<br>keep it together<br>when your whole world<br>has fallen apart?</p>

  <div class="director">
    <span class="director-label">directed by</span>
    <span class="director-name">Ned Pilbury</span>
  </div>
  <div class="dates">1 - 5 MARCH 2016</div>
  <div class="times">Tuesday to Friday 20:00 | Saturday 19:00</div>
  <div class="venue">Théâtre du Colibri Eaux-Vives, Geneva</div>
  <div class="links">
    for more info: <b>www.lspg.ch</b><br>
    for tickets: <b>www.scenesansfrontiere.ch</b>
  </div>
</main>
</body>
</html>
```